Exceptional Properties Flyer

I need a flyer template that I can re-use for high-end home listings over $1m in price. 11 X 17 horizontal folded to open wtih front photo shot large on front with short descriptionon areas, room for my photo, logo, contact info & property address then photo slots inside all pagers with room for copy to be plugged in. 3-4 photo spots per page at various sizes but room for bullet point descriptions on pages somewhere. Back of flyer larger photo slot and 2-3 smaller spots below with room for my photo and contact info
My contact info:
Maribel Oswick
Real Estate Broker
Halvorn Group Real Estate
Direct 206.555.0187
Email: maribel.oswic@tallowpine.com

```html
<!DOCTYPE html>
<html lang="en">
<head>
<meta charset="utf-8">
<title>Exceptional Properties Flyer</title>
<link rel="stylesheet" href="https://fonts.googleapis.com/css2?family=Montserrat:ital,wght@0,400;0,500;0,600;0,700;1,500&display=swap">
<style>
  :root {
    --stage: #464648;
    --paper: #ffffff;
    --ink: #111111;
    --black: #0a0a0a;
    --gold: #b29a28;
    --gold-light: #d2bb45;
    --grey-text: #3a3a3a;
    --photo-warm: #d9c4a2;
    --photo-cream: #ece2cf;
    --photo-wood: #9a6a3a;
    --photo-green: #6d7a5a;
  }
  * { margin: 0; padding: 0; box-sizing: border-box; }
  html, body { width: 1200px; height: 1200px; overflow: hidden; }
  body {
    background: radial-gradient(circle at 50% 45%, #545456, var(--stage) 75%);
    font-family: "Montserrat", sans-serif;
    color: var(--ink);
    position: relative;
  }
  .page { position: absolute; background: var(--paper); overflow: hidden; }
  .page--front-left { left: 195px; top: 72px; width: 405px; height: 524px; }
  .page--front-right { left: 601px; top: 72px; width: 405px; height: 524px; }
  .page--inside-left { left: 195px; top: 603px; width: 405px; height: 525px; }
  .page--inside-right { left: 601px; top: 603px; width: 405px; height: 525px; }
  .abs { position: absolute; }
  .photo { position: absolute; }
  .nowrap { white-space: nowrap; }

  /* Brand mark */
  .brand { display: flex; align-items: center; gap: 6px; font-weight: 700; color: var(--ink); white-space: nowrap; }
  .brand__square { width: 9px; height: 9px; background: var(--ink); flex: none; }

  /* Back cover */
  .contact-bar { left: 0; top: 366px; width: 405px; height: 158px; background: var(--black); }
  .url-tab { left: 0; top: 366px; width: 405px; height: 28px; }
  .url-tab span { position: absolute; left: 128px; top: 5px; width: 200px; text-align: center; font-size: 12px; color: var(--ink); }
  .portrait { background: linear-gradient(160deg, #a9bfd0, #c9b48a 55%, #2a2a2a); }
  .contact { left: 135px; top: 406px; color: #fff; white-space: nowrap; }
  .contact__firm { font-size: 14.5px; font-weight: 700; }
  .contact__name { font-size: 18.5px; font-weight: 600; color: var(--gold-light); margin-top: 2px; }
  .contact__title { font-size: 9.5px; font-style: italic; font-weight: 500; }
  .contact__phone { font-size: 18px; font-weight: 700; margin-top: 4px; }
  .contact__email { font-size: 10px; }

  /* Front cover */
  .cover-brand { left: 0; top: 36px; width: 405px; justify-content: center; font-size: 19px; }
  .address-band { left: 0; top: 366px; width: 290px; height: 26px; background: var(--gold); color: #fff; font-size: 12.5px; font-weight: 600; padding: 6px 0 0 18px; white-space: nowrap; }
  .cover-portrait { left: 290px; top: 315px; width: 91px; height: 117px; border: 1px solid #fff; }
  .description { left: 18px; top: 408px; width: 215px; }
  .description h2 { font-size: 15px; font-weight: 700; white-space: nowrap; }
  .description p { font-size: 8.6px; line-height: 1.35; color: var(--grey-text); margin-top: 4px; }
  .cover-contact { right: 24px; top: 437px; text-align: right; white-space: nowrap; }
  .cover-contact .name { font-size: 14.5px; font-weight: 600; }
  .cover-contact .title { font-size: 8px; font-style: italic; font-weight: 500; }
  .cover-contact .phone { font-size: 18.5px; font-weight: 700; margin-top: 4px; }
  .cover-contact .email { font-size: 8px; color: var(--grey-text); }

  /* Inside left */
  .page-head { left: 25px; top: 36px; font-size: 23.5px; font-weight: 700; white-space: nowrap; }
  .page-intro { left: 25px; top: 72px; font-size: 8.4px; line-height: 1.5; color: var(--grey-text); white-space: nowrap; }
  .feature-caption { left: 25px; top: 285px; width: 362px; height: 58px; background: var(--gold); color: #fff; padding: 10px 10px 0 10px; }
  .feature-caption h3 { font-size: 13px; font-weight: 600; white-space: nowrap; }
  .feature-caption p { font-size: 8.2px; line-height: 1.35; margin-top: 2px; white-space: nowrap; }
  .body-col { top: 352px; width: 171px; font-size: 7px; line-height: 1.52; color: var(--grey-text); text-align: justify; }
  .body-col--a { left: 25px; }
  .body-col--b { left: 217px; }

  /* Inside right */
  .room-caption { left: 17px; width: 235px; }
  .room-caption h4 { font-size: 9px; font-weight: 700; white-space: nowrap; }
  .room-caption p { font-size: 5.4px; line-height: 1.35; color: var(--grey-text); margin-top: 2px; white-space: nowrap; }
  .side-brand { left: 262px; top: 38px; width: 140px; justify-content: center; font-size: 11.5px; }
  .bullets { left: 270px; top: 146px; width: 128px; color: #fff; }
  .bullets h3 { font-size: 15px; font-weight: 600; color: var(--gold-light); line-height: 1.2; margin-bottom: 5px; }
  .bullets ul { list-style: none; }
  .bullets li { position: relative; padding-left: 12px; font-size: 9.6px; font-weight: 600; line-height: 1.22; margin-bottom: 6px; }
  .bullets li::before { content: "•"; position: absolute; left: 0; top: 0; font-size: 8px; }
</style>
</head>
<body>

<!-- Back cover -->
<section class="page page--front-left">
  <div class="photo" style="left:0;top:0;width:405px;height:246px;background:linear-gradient(180deg,#efe6d6,var(--photo-warm) 60%,#b9a07c);" role="img" aria-label="Large photo of a bright kitchen with dining table"></div>
  <svg class="abs" style="left:0;top:250px" width="405" height="112" viewBox="0 0 405 112">
    <defs>
      <linearGradient id="g-stair" x1="0" y1="0" x2="0" y2="1"><stop offset="0" stop-color="#d8c7aa"/><stop offset="1" stop-color="#8d7456"/></linearGradient>
      <linearGradient id="g-bath" x1="0" y1="0" x2="0" y2="1"><stop offset="0" stop-color="#b98a52"/><stop offset="1" stop-color="#6e4424"/></linearGradient>
      <linearGradient id="g-living" x1="0" y1="0" x2="0" y2="1"><stop offset="0" stop-color="#e6ded0"/><stop offset="1" stop-color="#c2ad8c"/></linearGradient>
    </defs>
    <polygon points="0,0 135,0 107,112 0,112" fill="url(#g-stair)" role="img" aria-label="Photo of a foyer with staircase"/>
    <polygon points="140,0 282,0 256,112 112,112" fill="url(#g-bath)" role="img" aria-label="Photo of a bathroom with vessel sink"/>
    <polygon points="287,0 405,0 405,112 261,112" fill="url(#g-living)" role="img" aria-label="Photo of a living room"/>
  </svg>
  <div class="abs contact-bar"></div>
  <svg class="abs url-tab" width="405" height="28" viewBox="0 0 405 28" aria-hidden="true">
    <polygon points="122,0 332,0 318,28 138,28" fill="var(--gold-light)"/>
  </svg>
  <div class="abs url-tab"><span>www.tallowpine.com</span></div>
  <div class="photo portrait" style="left:25px;top:378px;width:91px;height:120px;" role="img" aria-label="Agent portrait photo"></div>
  <div class="abs contact">
    <div class="contact__firm">HALVORN GROUP REAL ESTATE</div>
    <div class="contact__name">Maribel Oswick</div>
    <div class="contact__title">Real Estate Broker</div>
    <div class="contact__phone">206.555.0187</div>
    <div class="contact__email">maribel.oswic@tallowpine.com</div>
  </div>
</section>

<!-- Front cover -->
<section class="page page--front-right">
  <div class="abs brand cover-brand"><span class="brand__square"></span>Tallowpine Realty</div>
  <div class="photo" style="left:0;top:100px;width:405px;height:266px;background:linear-gradient(180deg,#e4e6ea 0%,#8a8a86 28%,var(--photo-green) 55%,#5e6a4c 100%);" role="img" aria-label="Large exterior photo of a two-storey craftsman home"></div>
  <div class="abs address-band">PROPERTY ADDRESS WILL GO HERE</div>
  <div class="photo portrait cover-portrait" role="img" aria-label="Agent portrait photo"></div>
  <div class="abs description">
    <h2>PROPERTY DESCRIPTION</h2>
    <p>Beatur aligniatur aut eos utem hillaut dunducia comnis qui sundeRo odi doluptur? Itatem qui dolut ut ut qui ipsumquati tempori tatiae pre sint velecea simpor</p>
  </div>
  <div class="abs cover-contact">
    <div class="name">Maribel Oswick</div>
    <div class="title">Real Estate Broker</div>
    <div class="phone">206.555.0187</div>
    <div class="email">maribel.oswic@tallowpine.com</div>
  </div>
</section>

<!-- Inside left -->
<section class="page page--inside-left">
  <h1 class="abs page-head">PAGE HEAD WILL GO HERE</h1>
  <p class="abs page-intro">Beatur aligniatur aut eos utem hillaut dunducia comnis qui sundeRo odi doluptur?<br>Itatem qui dolut ut ut qui ipsumquati tempori tatiae pre sint velecea simpor</p>
  <div class="photo" style="left:25px;top:105px;width:362px;height:178px;background:linear-gradient(180deg,#f1ece2,var(--photo-cream) 45%,#c6a764 80%,#b09a78);" role="img" aria-label="Photo of a formal living room with gold drapes"></div>
  <div class="abs feature-caption">
    <h3>YOUR SUBHEAD WILL GO HERE</h3>
    <p>Beatur aligniatur aut eos utem hillaut dunducia comnis qui sundeRo odi<br>doluptur? Itatem qui dolut ut ut qui ipsumquati tempori tatiae pre sint</p>
  </div>
  <p class="abs body-col body-col--a">Sunlight moves through every room of this home from morning to dusk. Wide oak floors run through the main level, and tall windows frame the garden and the water beyond. The kitchen opens to a family room with a stone fireplace and doors to a covered terrace. Upstairs the primary suite offers a spa bath, a dressing room and a quiet reading nook. Two guest rooms share a bright hall bath, and a bonus room sits above the garage for play or work. Mature trees, a level lawn and a three car garage complete the setting.</p>
  <p class="abs body-col body-col--b">Sunlight moves through every room of this home from morning to dusk. Wide oak floors run through the main level, and tall windows frame the garden and the water beyond. The kitchen opens to a family room with a stone fireplace and doors to a covered terrace. Upstairs the primary suite offers a spa bath, a dressing room and a quiet reading nook. Two guest rooms share a bright hall bath, and a bonus room sits above the garage for play or work. Mature trees, a level lawn and a three car garage complete the setting.</p>
</section>

<!-- Inside right -->
<section class="page page--inside-right">
  <svg class="abs" style="left:0;top:0" width="405" height="525" viewBox="0 0 405 525" aria-hidden="true">
    <path d="M258,133 C320,128 365,118 405,103 L405,525 L258,525 Z" fill="var(--black)"/>
    <path d="M128,0 C175,70 255,128 405,98" fill="none" stroke="#d6d6d6" stroke-width="2"/>
    <path d="M150,0 C200,85 280,132 405,104" fill="none" stroke="var(--gold-light)" stroke-width="6"/>
  </svg>
  <div class="photo" style="left:17px;top:24px;width:235px;height:112px;background:linear-gradient(180deg,#efe6d6,var(--photo-warm) 60%,#b9a07c);" role="img" aria-label="Photo of the kitchen and dining area"></div>
  <div class="abs room-caption" style="top:142px">
    <h4>YOUR SUBHEAD WILL GO HERE</h4>
    <p>Short room notes go here on finishes, light and layout.<br>Add a second line of simple copy for each room.</p>
  </div>
  <div class="photo" style="left:17px;top:185px;width:235px;height:112px;background:linear-gradient(180deg,#e8e2d8,#d8cbb5 55%,#b7a283);" role="img" aria-label="Photo of the family room with fireplace"></div>
  <div class="abs room-caption" style="top:306px">
    <h4>YOUR SUBHEAD WILL GO HERE</h4>
    <p>Short room notes go here on finishes, light and layout.<br>Add a second line of simple copy for each room.</p>
  </div>
  <div class="photo" style="left:17px;top:347px;width:235px;height:112px;background:linear-gradient(180deg,#b98a52,var(--photo-wood) 50%,#5e3a1e);" role="img" aria-label="Photo of the primary bathroom"></div>
  <div class="abs room-caption" style="top:466px">
    <h4>YOUR SUBHEAD WILL GO HERE</h4>
    <p>Short room notes go here on finishes, light and layout.<br>Add a second line of simple copy for each room.</p>
  </div>
  <div class="abs brand side-brand"><span class="brand__square"></span>Tallowpine Realty</div>
  <div class="abs bullets">
    <h3>BULLET<br>POINTS HEAD</h3>
    <ul>
      <li>Tem ellabor emolupid qui restiaes velese</li>
      <li>volum sim qui alita dolupta culluptae consequunte nobitem porectur?</li>
      <li>Ilianda erferia spicimp erferis event la dolendem et am</li>
      <li>quid quia dolorpo remqui ut ommoluptatio excero con porehen dandeliti aut et</li>
      <li>volum sim qui alita dolupta culluptae consequunte nobitem porectur?</li>
      <li>Ilianda erferia spicimp erferis event la dolende</li>
    </ul>
  </div>
</section>

</body>
</html>
```